THE WELLNESS BARN WEBSITE for Physio, Fitness, health

An attractive website advertising a physiotherapyand fitness / gym business, not generic, colours are natural, greens, browns, beiges. No cheesy pictures. With the ability to sell a small,amount of goods online if i decide to. Simple to navigate. Text boxes that i can input the main information and change easily. Somewhere to put my timetable. Easy to find contact details. However many pages it needs, im not fussed.
Target Market(s)
People looking for rehabilitation or fitness classes
Industry/Entity Type
Physiotherapy, Fitness, Gym, Health
Coding
Coded - Design and coding required
Number of Pages Required
1 page
Font styles to use
Other font styles liked:
- Im not fusse,ld, not script
Requirements
Must have
- Will upload posts from my business insta page for reference about the feel. Earthy natural tones, I have a lot of timber, and rustic looking piece's, plants etc in my clinic
Nice to have
- Simple to navigate
Should not have
- Cheesy "yoga" or generic "people doing physio" pics

```html
<!DOCTYPE html>
<html lang="en">
<head>
<meta charset="utf-8">
<title>The Wellness Barn Wattle Bay</title>
<link href="https://fonts.googleapis.com/css2?family=Montserrat:ital,wght@0,400;0,500;0,600;0,700;0,800;1,400&family=Kanit:wght@400;500;600;700&display=swap" rel="stylesheet">
<style>
:root{
  --forest:#27431a;
  --forest-deep:#1f3814;
  --leaf:#93c83e;
  --ink:#1d1d1d;
  --muted:#555;
  --mist:#f2f3ef;
  --night:#141414;
  --star:#e8a317;
}
*{box-sizing:border-box;margin:0;padding:0}
html,body{width:1200px;height:4658px;overflow:hidden}
body{font-family:"Montserrat",sans-serif;color:var(--ink);background:#fff;position:relative}
.abs{position:absolute}
.btn{display:inline-block;font-weight:700;font-size:13px;letter-spacing:.5px;text-transform:uppercase;padding:12px 24px}

/* header */
.site-header{position:absolute;top:0;left:0;width:1200px;height:72px;background:#fff;border-bottom:1px solid #e5e5e5}
.brand{position:absolute;left:66px;top:14px;display:flex;align-items:center;gap:8px;font-family:"Kanit",sans-serif;font-weight:600;font-size:17px;color:var(--forest);line-height:1}
.brand-dot{width:40px;height:40px;border-radius:50%;background:var(--forest)}
.main-nav{position:absolute;left:282px;top:26px;display:flex;gap:36px;font-size:13px;font-weight:500;text-transform:uppercase}
.main-nav .active{border-bottom:2px solid var(--forest);padding-bottom:4px}
.header-cta{position:absolute;left:758px;top:12px;background:var(--forest);color:#fff;width:152px;text-align:center;padding:15px 0}
.agent{position:absolute;left:922px;top:16px;display:flex;gap:12px;align-items:center}
.agent-icon{width:36px;height:36px;border:2px solid var(--ink);border-radius:50%;display:flex;align-items:center;justify-content:center}
.agent small{display:block;font-size:10px;letter-spacing:2px;color:var(--muted)}
.agent strong{font-size:22px;font-weight:700}

/* hero */
.hero{position:absolute;top:72px;left:0;width:1200px;height:602px;background:linear-gradient(180deg,#4a3a2a 0%,#6b5640 45%,#3a2f24 100%);text-align:center;color:#fff}
.hero-eyebrow{position:absolute;top:100px;width:100%;font-size:16px}
.hero h1{position:absolute;top:122px;width:100%;font-family:"Montserrat",sans-serif;font-weight:800;font-size:40px}
.hero h1 span{color:var(--leaf)}
.hero p{position:absolute;top:180px;left:290px;width:620px;font-size:13px;line-height:20px}
.hero .btn{position:absolute;top:262px;left:514px;width:172px;background:var(--forest);color:#fff;border:2px solid #fff;padding:14px 0}
.dots{position:absolute;display:flex;gap:10px}
.dots i{width:12px;height:12px;border-radius:50%;border:1px solid #fff;display:block}
.dots i.on{background:var(--leaf);border-color:var(--leaf)}

/* about */
.about{position:absolute;top:674px;left:0;width:1200px;height:759px;background:var(--forest)}
.about-frame{position:absolute;left:414px;top:344px;width:188px;height:170px;background:#fff}
.about-photo{position:absolute;left:98px;top:122px;width:482px;height:375px;border-radius:6px;background:linear-gradient(135deg,#5d5d5b,#2a2a2a 60%,#3f4a2e)}
.about-copy{position:absolute;left:652px;top:114px;width:450px;color:#fff}
.about-copy h2{font-size:34px;font-weight:400}
.about-copy h2 b{font-weight:800}
.about-copy h3{font-size:20px;font-weight:600;margin-top:22px}
.about-copy p{font-size:13.5px;line-height:25px;margin-top:18px}
.about-copy .btn{margin-top:20px;background:#fff;color:var(--forest);padding:13px 28px}

/* service cards */
.service{position:absolute;top:1285px;width:230px;height:377px;background:#fff;border:2px solid #ddd;padding:7px;text-align:center;box-shadow:0 4px 10px rgba(0,0,0,.12)}
.service .pic{height:212px;border-radius:2px}
.service h4{font-family:"Kanit",sans-serif;font-weight:500;font-size:19px;line-height:24px;margin-top:14px}
.service p{font-size:11.5px;line-height:18px;color:var(--muted);margin:10px 14px 0}

/* section head */
.sec-head{position:absolute;width:100%;text-align:center}
.sec-head h2{font-size:34px;font-weight:400}
.sec-head h2 b{font-weight:800}
.rule{width:100px;height:2px;background:#bbb;margin:10px auto 0}

/* team */
.member{position:absolute;top:1921px;width:290px;text-align:center}
.member .face{width:136px;height:136px;border-radius:50%;border:3px solid var(--forest);margin:0 auto;background:linear-gradient(160deg,#d9d4cc,#8a7c6e)}
.member h4{font-size:22px;font-weight:700;margin-top:26px}
.member .role{font-size:15px;margin-top:6px}
.member p{font-size:11.5px;line-height:18px;color:var(--muted);margin-top:10px}
.socials{display:flex;gap:10px;justify-content:center;margin-top:16px}
.socials i{width:34px;height:34px;border-radius:50%;background:var(--forest);display:block}

/* products */
.products{position:absolute;top:2340px;left:0;width:1200px;height:645px;background:var(--forest);overflow:hidden}
.products h2{position:absolute;left:108px;top:94px;color:#fff;font-size:34px;font-weight:400}
.products h2 b{font-weight:800}
.products .line{position:absolute;left:108px;top:150px;width:104px;height:2px;background:#5b7a47}
.arrow{position:absolute;top:140px;width:44px;height:44px;border:2px solid #fff;border-radius:50%;display:flex;align-items:center;justify-content:center}
.product{position:absolute;top:198px;width:228px;height:320px;background:#fff;padding:8px;text-align:center}
.product .pic{height:212px}
.product h4{font-family:"Kanit",sans-serif;font-weight:500;font-size:19px;margin-top:16px}
.product p{font-size:11.5px;line-height:18px;color:var(--muted);margin:6px 14px 0}
.product.faded{opacity:.35}

/* stories */
.stories{position:absolute;top:2985px;left:0;width:1200px;height:638px;background:var(--mist)}
.quote{position:absolute;top:217px;width:450px;height:193px;background:#fff;border-radius:10px;padding:40px 18px 20px;box-shadow:0 4px 14px rgba(0,0,0,.12)}
.quote .title{font-size:16px;font-weight:500}
.quote .stars{position:absolute;right:18px;top:40px;color:var(--star);font-size:18px;letter-spacing:2px}
.quote p{font-style:italic;font-size:13.5px;line-height:23px;text-align:right;margin-top:18px;color:#333}
.author{position:absolute;top:432px;display:flex;gap:12px;align-items:center}
.author .face{width:56px;height:56px;border-radius:50%;border:3px solid #fff;background:linear-gradient(160deg,#cbb7a4,#7e6a58)}
.author b{font-size:16px;font-weight:500;display:block}
.author span{font-size:13px;color:var(--muted)}

/* faq */
.faq{position:absolute;top:3623px;left:0;width:1200px;height:605px;background:linear-gradient(180deg,#fff 0%,#fff 55%,#e8d8c2 75%,#b0845a 100%)}
.faq-item{position:absolute;left:222px;width:786px;border-bottom:1px solid #ccc;padding:0 46px 16px}
.faq-item h5{font-size:19px;font-weight:600}
.faq-item p{font-size:14px;line-height:24px;color:#333;margin-top:8px}
.chev{position:absolute;right:80px;top:4px;width:18px;height:18px;border-radius:50%;background:var(--forest-deep);display:flex;align-items:center;justify-content:center}

/* footer */
.site-footer{position:absolute;top:4228px;left:0;width:1200px;height:430px;background:var(--night);color:#fff}
.foot-brand{position:absolute;left:176px;top:190px;font-family:"Kanit",sans-serif;font-weight:600;font-size:22px;text-align:center;line-height:26px}
.foot-col{position:absolute;top:104px}
.foot-col h6{font-family:"Kanit",sans-serif;font-size:20px;font-weight:500}
.foot-col .u{width:66px;height:2px;background:#666;margin:10px 0 22px}
.foot-col li{list-style:none;font-size:12px;line-height:26px}
.foot-col p{font-size:12px;line-height:19px;width:280px}
.email{margin-top:18px;width:334px;height:38px;background:#5e7a4a;font-size:11px;padding:12px 20px;color:#e8eee2}
.sub{margin-top:10px;width:146px;height:38px;background:var(--forest);font-size:12px;font-weight:700;text-align:center;padding-top:12px}
.foot-rule{position:absolute;left:110px;top:340px;width:980px;height:1px;background:#3a3a3a}
.copy{position:absolute;left:110px;top:370px;font-size:13px}
.foot-social{position:absolute;left:1012px;top:362px;display:flex;gap:10px}
.foot-social i{width:34px;height:34px;border-radius:50%;background:var(--forest);display:block}
</style>
</head>
<body>

<header class="site-header">
  <div class="brand"><span class="brand-dot"></span>The Wellness<br>Barn</div>
  <nav class="main-nav">
    <span class="active">Home</span><span>About Us</span><span>Products</span><span>Our Offer?</span><span>Team</span>
  </nav>
  <span class="btn header-cta">Contact Us</span>
  <div class="agent">
    <span class="agent-icon"><svg width="16" height="16" viewBox="0 0 24 24"><path d="M6.6 10.8a15 15 0 006.6 6.6l2.2-2.2a1 1 0 011-.25 11.4 11.4 0 003.6.57 1 1 0 011 1V20a1 1 0 01-1 1A17 17 0 013 4a1 1 0 011-1h3.5a1 1 0 011 1c0 1.25.2 2.45.57 3.57a1 1 0 01-.25 1z" fill="#1d1d1d"/></svg></span>
    <div><small>TALK TO AN AGENT</small><strong>040.000.1234</strong></div>
  </div>
</header>

<section class="hero" role="img" aria-label="Photo of the gym interior with rowing machines, rings and weights">
  <div class="hero-eyebrow">WELCOME TO</div>
  <h1>THE WELLNESS BARN <span>WATTLE BAY</span></h1>
  <p>Discover a healthier you with our Physiotherapist led programs. At The Wellness Barn Wattle Bay, we focus on safe and effective movement to enhance your quality of life. Join us for a comprehensive approach to wellbeing.</p>
  <span class="btn">Get Started</span>
  <div class="dots" style="left:560px;top:564px"><i></i><i class="on"></i><i></i><i></i></div>
</section>

<section class="about">
  <div class="about-frame"></div>
  <div class="about-photo" role="img" aria-label="Photo of a trainer in a branded black shirt beside gym equipment"></div>
  <div class="about-copy">
    <h2>ABOUT <b>US</b></h2>
    <h3>What do we have to offer?</h3>
    <p>The Wellness Barn Wattle Bay is dedicated to empowering individuals to achieve their health and wellbeing goals through safe and effective movement. Our core values include Integrity, Collaboration, Inclusivity, and a strong Commitment to health. We believe in providing professional support tailored to each individual's needs. Our team, including experienced professionals like Dr. Clara Whitfield and Owen Barker, is committed to guiding you on your wellness journey. Join us in fostering a healthier community where everyone can thrive.</p>
    <span class="btn">Learn More</span>
  </div>
</section>

<article class="service" style="left:105px"><div class="pic" role="img" aria-label="Photo of a group exercise class" style="background:linear-gradient(160deg,#dfe3e6,#9aa4a8)"></div><h4>Physiotherapy Classes for Everyone</h4><p>Our classes are tailored for all ages, focusing on safe movement to enhance mobility and overall health.</p></article>
<article class="service" style="left:358px"><div class="pic" role="img" aria-label="Photo of a wellness consultation" style="background:linear-gradient(160deg,#6a4a33,#2e2219)"></div><h4>Holistic Wellness Programs</h4><p>Our programs integrate physical activity with nutritional guidance to support sustainable health improvement</p></article>
<article class="service" style="left:614px"><div class="pic" role="img" aria-label="Photo of a calm studio session" style="background:linear-gradient(160deg,#eee9df,#b9ad98)"></div><h4>Mindfulness and Yoga Sessions</h4><p>Join our yoga sessions to improve mental clarity and physical flexibility in a calming environment.</p></article>
<article class="service" style="left:868px"><div class="pic" role="img" aria-label="Photo of a nutrition consultation" style="background:linear-gradient(160deg,#5a4636,#2b2620 60%,#4d6a2e)"></div><h4>Personalized Nutrition Guidance</h4><p>Receive expert dietary advice tailored to your needs, helping you make informed health choices.</p></article>

<div class="sec-head" style="top:1736px">
  <h2>MEET <b>OUR TEAM</b></h2><div class="rule"></div>
  <p style="font-size:20px;font-weight:500;margin-top:14px">Get to Know Us</p>
  <p style="font-size:17px;margin-top:16px">Discover the dedicated professionals committed to your health.</p>
</div>

<div class="member" style="left:138px"><div class="face" role="img" aria-label="Portrait photo of the lead physiotherapist"></div><h4>Dr. Clara Whitfield</h4><div class="role">Lead Physiotherapist</div><p>Dr. Clara specializes in sports rehabilitation and has over 10 years of experience in helping clients recover from injuries.</p><div class="socials"><i></i><i></i></div></div>
<div class="member" style="left:455px"><div class="face" role="img" aria-label="Portrait photo of the wellness coach"></div><h4>Daniel Moss</h4><div class="role">Wellness Coach</div><p>Daniel focuses on holistic health and wellness, guiding clients through lifestyle changes to improve their overall wellbeing.</p><div class="socials"><i></i><i></i></div></div>
<div class="member" style="left:771px"><div class="face" role="img" aria-label="Portrait photo of the physiotherapy assistant"></div><h4>Grace Linden</h4><div class="role">Physiotherapy Assistant</div><p>Grace assists in physiotherapy sessions and is passionate about helping clients achieve their health goals.</p><div class="socials"><i></i><i></i></div></div>

<section class="products">
  <h2>OUR <b>PRODUCTS</b></h2><div class="line"></div>
  <span class="arrow" style="left:986px"><svg width="14" height="14" viewBox="0 0 14 14"><path d="M9 2L4 7l5 5" stroke="#fff" stroke-width="2" fill="none"/></svg></span>
  <span class="arrow" style="left:1044px"><svg width="14" height="14" viewBox="0 0 14 14"><path d="M5 2l5 5-5 5" stroke="#fff" stroke-width="2" fill="none"/></svg></span>
  <article class="product faded" style="left:-150px"><div class="pic" style="background:#6b5a3f"></div><h4>Kcasec Cecesis Raeins</h4><p>Haciatis unde omnis iste natus error sit voluptatem.</p></article>
  <article class="product" style="left:110px"><div class="pic" role="img" aria-label="Photo of a spray bottle among plants" style="background:linear-gradient(160deg,#6f8c44,#2c3b1d)"></div><h4>Kcasec Cecesis Raeins</h4><p>Haciatis unde omnis iste natus error sit voluptatem.</p></article>
  <article class="product" style="left:362px"><div class="pic" role="img" aria-label="Photo of branded caps" style="background:linear-gradient(160deg,#c9c9c3,#4a5238)"></div><h4>Kcasec Cecesis Raeins</h4><p>Haciatis unde omnis iste natus error sit voluptatem.</p></article>
  <article class="product" style="left:613px"><div class="pic" role="img" aria-label="Photo of a gift box of wellness items" style="background:linear-gradient(160deg,#ece4cf,#8f97b8)"></div><h4>Kcasec Cecesis Raeins</h4><p>Haciatis unde omnis iste natus error sit voluptatem.</p></article>
  <article class="product" style="left:864px"><div class="pic" role="img" aria-label="Photo of a heat bag product" style="background:linear-gradient(160deg,#e6d8c4,#b06a40)"></div><h4>Kcasec Cecesis Raeins</h4><p>Haciatis unde omnis iste natus error sit voluptatem.</p></article>
  <article class="product faded" style="left:1114px"><div class="pic" style="background:#59623c"></div><h4>Kcasec Cecesis Raeins</h4><p>Haciatis unde omnis iste natus error sit voluptatem.</p></article>
</section>

<section class="stories">
  <div class="sec-head" style="top:102px">
    <h2>CLIENT <b>SUCCESS STORIES</b></h2>
    <p style="font-size:20px;font-weight:500;margin-top:28px">Hear from our clients about their transformative journeys with us.</p>
  </div>
  <div class="quote" style="left:110px"><div class="title">Amazing Experience!</div><div class="stars">★★★★★</div><p>"The Wellness Barn has completely changed my approach to fitness. Their programs are tailored and effective!"</p></div>
  <div class="author" style="left:230px"><div class="face" role="img" aria-label="Client portrait photo"></div><div><b>Holly Ashford</b><span>Fitness Enthusiast</span></div></div>
  <div class="quote" style="left:630px"><div class="title">Amazing Experience!</div><div class="stars">★★★★★</div><p>"Their holistic approach to health is refreshing. I appreciate the focus on both physical and mental well-being."</p></div>
  <div class="author" style="left:750px"><div class="face" role="img" aria-label="Client portrait photo"></div><div><b>Ruth Callaway</b><span>Health Advocate</span></div></div>
  <div class="dots" style="left:570px;top:527px"><i style="border-color:#333"></i><i style="border-color:#333"></i><i style="background:var(--forest-deep);border-color:var(--forest-deep)"></i></div>
</section>

<section class="faq" role="img" aria-label="Soft sunset field photo fading in at the bottom">
  <div class="sec-head" style="top:92px">
    <h2><b>FAQ'S</b></h2><div class="rule" style="width:90px"></div>
    <p style="font-size:17px;font-weight:600;line-height:29px;margin:22px auto 0;width:680px">Find answers to common questions about our health and wellness programs, services, and how we can support your journey to better health.</p>
  </div>
  <div class="faq-item" style="top:230px"><h5>What types of programs do you offer?</h5><p>We offer a variety of programs including physiotherapy classes, wellness programs,<br>and tailored fitness plans designed for all ages and abilities.</p><span class="chev"><svg width="8" height="8" viewBox="0 0 8 8"><path d="M1 5l3-3 3 3" stroke="#fff" stroke-width="1.5" fill="none"/></svg></span></div>
  <div class="faq-item" style="top:346px"><h5>Eaoluptatem accusantium antium?</h5><span class="chev"><svg width="8" height="8" viewBox="0 0 8 8"><path d="M1 3l3 3 3-3" stroke="#fff" stroke-width="1.5" fill="none"/></svg></span></div>
  <div class="faq-item" style="top:400px;border:0"><h5>Kaerspiciatis unde omnis iste?</h5><span class="chev"><svg width="8" height="8" viewBox="0 0 8 8"><path d="M1 3l3 3 3-3" stroke="#fff" stroke-width="1.5" fill="none"/></svg></span></div>
  <span class="btn abs" style="left:514px;top:463px;width:172px;text-align:center;background:var(--forest-deep);color:#fff;padding:15px 0">View Programs</span>
</section>

<footer class="site-footer">
  <div class="foot-brand">The Wellness<br>Barn</div>
  <div class="foot-col" style="left:386px"><h6>Quick links</h6><div class="u"></div><ul><li>Home</li><li>About Us</li><li>Products</li><li>Our offer?</li><li>Team</li><li>Contact Us</li></ul></div>
  <div class="foot-col" style="left:574px"><h6>Links</h6><div class="u"></div><ul><li>Copyright</li><li>Legal</li><li>Privacy</li><li>Accessibility</li><li>Sitemap</li></ul></div>
  <div class="foot-col" style="left:756px"><h6>Stay Updated</h6><div class="u"></div><p>Subscribe to our newsletter for the latest health tips and program updates.</p><div class="email">Enter Email</div><div class="sub">SUBSCRIBE</div></div>
  <div class="foot-rule"></div>
  <div class="copy">© 2025 The Wellness Barn Wattle Bay. All rights reserved.</div>
  <div class="foot-social"><i></i><i></i></div>
</footer>

</body>
</html>
```